Harborview Estates Business Card for Apartment Buildings

Create business cards for resident managers who run apartment buildings. The audience is the public who are searching for apartment rentals, and current residents who live at the apartment building. Key design element will be incorporating the company logo, however, the logo cannot dominate. The building name and manager name are more important than the logo. Current business card design leaves little room for copy, so we may need to reduce the size on the current card to allow for more space for copy.

Target Market(s)

Adults 18-65 years of age, who are looking for an apartment rental, plus current residents who live at our apartment buildings.

Industry/Entity Type

Property Management

Contact Information for Business Card

A major design element will be use of the company logo. Important property and manager contact information must be part of the design. The size of the logo will need to be reduced to make room for building and manager contact copy.

Font styles to use
Sans Serif

Colors
3176b5
000000
959595
ffffff

Requirements
Must have
• 1) Incorporate the company logo.
• 2) Use the company colors (dark blue, black/grey, over white).
• 3) FEATURE THE BUILDING NAME
• 4) FEATURE THE MANAGER NAME
• 5) The company name is less important than BUILDING and MANAGER
• 6) Manager contact information
• **SEE ATTACHED CREATIVE BRIEF**
Nice to have
• 1) Back of card logo watermark
• 2) Ability to write notes on back of carfd
Should not have
• Avoid letting the company logo dominate the card, the building name and manager are more important than the company logo.

```html
<!DOCTYPE html>
<html lang="en">
<head>
<meta charset="utf-8">
<title>Harborview Estates Business Card</title>
<link rel="stylesheet" href="https://fonts.googleapis.com/css2?family=Roboto:wght@400;500;700&family=Roboto+Condensed:wght@400;700&display=swap">
<style>
  :root {
    --brand-blue: #0f6dab;
    --strip-grey: #474747;
    --paper: #f4f4f4;
    --ink-light: #ffffff;
    --watermark: #e2e2e2;
    --backdrop: #2a2a2a;
  }
  html, body {
    margin: 0;
    width: 1200px;
    height: 960px;
    overflow: hidden;
    background: var(--backdrop);
    font-family: "Roboto", Arial, sans-serif;
  }
  .stage { position: relative; width: 1200px; height: 960px; }

  .card { position: absolute; width: 600px; height: 342px; background: var(--paper); overflow: hidden; }

  /* back of card */
  .card-back { left: 320px; top: 104px; }
  .card-back .watermark-name {
    position: absolute; inset: 0;
    display: flex; align-items: center; justify-content: center;
    font-weight: 700; font-size: 44px; letter-spacing: 2px;
    color: var(--watermark);
  }

  /* front of card */
  .card-front { left: 320px; top: 493px; }
  .icon-strip { position: absolute; left: 0; top: 0; width: 31px; height: 100%; background: var(--strip-grey); }
  .edge-strip { position: absolute; right: 0; top: 0; width: 18px; height: 100%; background: var(--strip-grey); }
  .info-panel { position: absolute; left: 31px; top: 0; width: 255px; height: 100%; background: var(--brand-blue); color: var(--ink-light); }

  .icon { position: absolute; left: 8px; width: 15px; height: 15px; fill: var(--ink-light); }

  .manager-name { position: absolute; left: 26px; top: 55px; margin: 0; font-family: "Roboto Condensed", Arial, sans-serif; font-weight: 700; font-size: 23px; }
  .manager-title { position: absolute; left: 26px; top: 82px; margin: 0; font-family: "Roboto Condensed", Arial, sans-serif; font-size: 16px; }
  .building { position: absolute; left: 26px; top: 123px; font-size: 14.5px; line-height: 18.5px; }
  .building-name { font-weight: 700; }
  .contacts { position: absolute; left: 26px; top: 205px; font-size: 14.5px; line-height: 19.5px; }

  .company-mark { position: absolute; left: 322px; top: 146px; width: 240px; display: flex; align-items: center; gap: 10px; }
  .company-mark .dot { flex: none; width: 14px; height: 14px; background: var(--strip-grey); }
  .company-mark .company-name { font-weight: 700; font-size: 19px; line-height: 22px; color: var(--brand-blue); letter-spacing: 0.5px; }
  .company-mark .company-name span { display: block; }
</style>
</head>
<body>
<div class="stage">

  <section class="card card-back" aria-label="Back of card">
    <div class="watermark-name">HARBORVIEW ESTATES</div>
  </section>

  <section class="card card-front" aria-label="Front of card">
    <div class="icon-strip">
      <svg class="icon" style="top:71px" viewBox="0 0 16 16"><circle cx="8" cy="4.5" r="3.5"/><path d="M1 15c0-4 3-6 7-6s7 2 7 6z"/></svg>
      <svg class="icon" style="top:144px" viewBox="0 0 16 16"><path d="M8 0a5.5 5.5 0 0 0-5.5 5.5C2.5 10 8 16 8 16s5.5-6 5.5-10.5A5.5 5.5 0 0 0 8 0zm0 8a2.5 2.5 0 1 1 0-5 2.5 2.5 0 0 1 0 5z"/></svg>
      <svg class="icon" style="top:211px;width:13px;height:13px" viewBox="0 0 16 16"><path d="M3.5 0.5l3 3-2 2c1 2.5 3 4.5 5.5 5.5l2-2 3 3-2 3C6 14 1.5 9 0.5 2.5z"/></svg>
      <svg class="icon" style="top:230px;height:14px" viewBox="0 0 16 16"><path d="M4 0h8v16H4zM5.5 1.5v11h5v-11zM7.5 13.5h1v1h-1z" fill-rule="evenodd"/></svg>
      <svg class="icon" style="top:249px;height:13px" viewBox="0 0 16 16"><path d="M4 0h8v4H4zM1 5h14v7h-3v4H4v-4H1zM5 10v4h6v-4z" fill-rule="evenodd"/></svg>
      <svg class="icon" style="top:270px;height:12px" viewBox="0 0 16 12"><path d="M0 0h16v12H0zM1.5 1.5L8 7l6.5-5.5z" fill-rule="evenodd"/></svg>
      <svg class="icon" style="top:289px;width:14px;height:14px" viewBox="0 0 16 16"><circle cx="8" cy="8" r="7.5"/><path d="M5 4c2 0 2 2 1 3s1 2 0 4M11 3c-1 2 1 3 2 4" stroke="#474747" stroke-width="1.5" fill="none"/></svg>
    </div>

    <div class="info-panel">
      <h1 class="manager-name">Marisol Quintero</h1>
      <p class="manager-title">Resident Manager</p>
      <div class="building">
        <div class="building-name">Bayside Court Apartments</div>
        <div>2845 Lantern Avenue</div>
        <div>Oceanside, CA 92058</div>
      </div>
      <div class="contacts">
        <div>555-214-3870</div>
        <div>555-381-6042</div>
        <div>555-627-9150</div>
        <div>marisol@harborviewest.com</div>
        <div>www.harborviewest.com</div>
      </div>
    </div>

    <div class="company-mark">
      <span class="dot"></span>
      <span class="company-name"><span>HARBORVIEW</span><span>ESTATES LLC</span></span>
    </div>

    <div class="edge-strip"></div>
  </section>

</div>
</body>
</html>
```